Recruiting Firm Need Professional, Modern Tri-Fold Brochure for their United States Based Business

-We need a professional, modern TRI-FOLD brochure design that can help generate business for our recruiting firm. We need an impressive brochure.
- Please use the about us website content and attached website content. Website: www.morvellstaffingpartners.example
- Please use logo files attached.
- Please note: This brochure will be the starting point for an upgraded website design so we are NOT looking for a brochure to look like our current website.
- We want potential clients to want to do business with us just based on the brochure look and feel alone.

Target Market(s)

small, medium, and large companies who need administrative, human resources, and accounting talent

Industry/Entity Type

Professional Service

Font styles to use
Serif

Requirements
Must have
• - Professional, Modern TRI-FOLD Brochure Design for United States Based Company
• - Please show diverse group of professionals pictures similar to the ones on our website. One pic must include an African American female and one pic must include an African male. Or both an African American female and male can be include in the group of other races. But All the group photos must be diverse in race and include both male and female.
• - Please show pics of one business professional too
• a diverse group photo would be nice on the front cover...so we can show diversity and inclusion from the start
Should not have
• - Please DO NOT use the same pictures on our website.

```html
<!DOCTYPE html>
<html lang="en">
<head>
<meta charset="utf-8">
<title>Morvell Staffing Partners – Tri-Fold Brochure</title>
<link rel="stylesheet" href="https://fonts.googleapis.com/css2?family=Lato:wght@400;700&family=Oswald:wght@500;700&family=Lora:wght@400;700&family=Great+Vibes&display=swap">
<style>
:root{
  --red:#c8161d;
  --red-dark:#9e0f14;
  --ink:#333333;
  --grey:#8a8a8a;
  --grey-light:#d9d9d9;
  --paper:#ffffff;
  --backdrop:#e4e4e4;
}
*{box-sizing:border-box;margin:0;padding:0}
html,body{width:998px;height:1200px;overflow:hidden}
body{background:var(--backdrop);font-family:"Lato",sans-serif;color:var(--ink);position:relative}
.spread{position:absolute;left:119px;width:760px;height:560px;display:flex;box-shadow:0 4px 14px rgba(0,0,0,.18);background:var(--paper)}
.spread--outside{top:30px}
.spread--inside{top:610px}
.panel{position:relative;width:253.33px;height:100%;overflow:hidden;background:linear-gradient(180deg,#fff 0%,#f4f4f4 60%,#fff 100%)}
.panel + .panel{border-left:1px solid #eee}
.photo{position:absolute;display:block}
.swoosh{position:absolute;left:0;width:100%}
p{font-size:7.4px;line-height:1.45}
.brand{display:flex;align-items:center;gap:5px;font-family:"Lora",serif;font-weight:700;color:var(--ink);letter-spacing:.5px}
.brand__square{width:12px;height:12px;background:var(--red);flex:none}

/* outside – about */
.about__head{position:absolute;top:190px;left:0;right:0;text-align:center;padding:0 18px}
.about__label{font-family:"Lato",sans-serif;font-size:14px;letter-spacing:2px;color:var(--ink)}
.about__title{font-family:"Lato",sans-serif;font-weight:700;color:var(--red);font-size:11.5px;line-height:1.25;margin:4px 0 8px}
.about__text{text-align:center}
.about__partner{font-size:11px;color:var(--red);letter-spacing:1px;margin:10px 0 5px;font-weight:400}

/* outside – mailer */
.mailer__stamp{position:absolute;top:18px;right:18px;width:52px;height:58px;border:1px solid #555}
.mailer__brand{position:absolute;top:20px;left:18px;writing-mode:vertical-rl;font-size:10px}
.mailer__contact{position:absolute;top:150px;left:105px;writing-mode:vertical-rl;display:flex;gap:12px}
.mailer__name{font-weight:700;color:var(--red);font-size:10.5px}
.mailer__phone{font-weight:700;color:var(--red);font-size:11px}
.mailer__phone strong{color:var(--ink);font-size:12px}
.mailer__web{font-size:7.5px;color:var(--ink)}
.mailer__web b{color:var(--red)}

/* outside – cover */
.cover__brand{position:absolute;top:18px;left:0;right:0;justify-content:center;font-size:11px}
.cover__welcome{position:absolute;top:335px;right:22px;font-family:"Great Vibes",cursive;color:var(--red);font-size:26px}
.cover__name{position:absolute;top:372px;right:20px;text-align:right;font-family:"Lora",serif;font-weight:700;font-size:21px;color:var(--ink);line-height:1.1}
.cover__name span{display:block;font-weight:400;font-size:19px;color:#666}
.cover__url{position:absolute;top:448px;right:20px;font-size:8px;letter-spacing:1px;color:var(--red)}

/* inside – intro */
.intro__title{position:absolute;top:22px;left:16px;right:16px;text-align:center;font-family:"Oswald",sans-serif;font-weight:700;color:var(--red);font-size:15px;line-height:1.15}
.intro__text{position:absolute;top:108px;left:20px;right:20px;text-align:center}
.intro__ask{position:absolute;top:210px;left:0;right:0;text-align:center;font-family:"Oswald",sans-serif;font-weight:700;color:var(--red);font-size:27px;line-height:1.05}
.intro__tag{position:absolute;top:318px;left:22px;right:22px;text-align:center;font-family:"Oswald",sans-serif;font-weight:500;font-size:9.5px;line-height:1.35}

/* inside – services */
.service{position:absolute;left:18px;right:16px;display:flex;gap:14px;align-items:flex-start}
.service svg{flex:none}
.service h3{font-family:"Lato",sans-serif;font-weight:700;font-size:9px;margin-bottom:3px}
.how{position:absolute;top:322px;left:18px;right:18px}
.how h3{color:var(--red);font-weight:700;font-size:10px;margin-bottom:4px}
.how li{font-size:7.4px;line-height:1.45;margin:0 0 5px 10px}
.services__brand{position:absolute;top:470px;left:0;right:0;justify-content:center;font-size:11px}
.services__url{position:absolute;top:500px;left:0;right:0;text-align:center;font-size:8px;letter-spacing:1px;color:#555}

/* inside – process */
.process__title{position:absolute;top:18px;left:14px;right:14px;text-align:center;font-family:"Oswald",sans-serif;font-weight:700;color:var(--red);font-size:14px;line-height:1.15}
.steps{position:absolute;top:70px;left:12px;right:14px;list-style:none}
.step{display:flex;gap:8px;margin-bottom:7px;align-items:flex-start}
.step__tag{flex:none;width:36px;text-align:center;font-size:7px;font-weight:700;color:var(--red)}
.step__tag i{display:block;width:14px;height:14px;margin:0 auto 2px;border-radius:50%;background:var(--red)}
.step p{font-size:7.2px}
.difference{position:absolute;top:408px;left:16px;right:14px}
.difference h3{font-family:"Lora",serif;font-weight:700;color:var(--red);font-size:12px;margin-bottom:6px}
.difference li{font-size:7.2px;line-height:1.45;margin:0 0 3px 10px}
</style>
</head>
<body>

<!-- OUTSIDE -->
<section class="spread spread--outside">

  <article class="panel about">
    <div class="photo" role="img" aria-label="Photo of two smiling professional women reviewing a laptop outdoors" style="top:0;left:0;width:100%;height:180px;background:linear-gradient(135deg,#6f8a4e,#b7c79a 45%,#5d5a57)"></div>
    <svg class="swoosh" style="top:140px" height="60" viewBox="0 0 253 60" preserveAspectRatio="none" aria-hidden="true">
      <path d="M0 60 L0 40 Q120 -10 253 20 L253 60 Z" fill="#fff"/>
      <path d="M0 40 Q120 -10 253 20" stroke="var(--red)" stroke-width="5" fill="none"/>
    </svg>
    <div class="about__head">
      <h2 class="about__label">ABOUT US:</h2>
      <h3 class="about__title">A Top-Notch Resource for Administrative, Human Resources, and Accounting Talent</h3>
      <p class="about__text">Morvell Staffing Partners is a professional search firm that specializes in providing top-notch administrative, human resources, and accounting talent. The cornerstone of our business is to provide best-in-class talent to companies seeking to simplify their recruiting process, increase efficiency, and optimize productivity. We develop a partnership with our client and candidate in order to make the recruitment process a success for both parties.</p>
      <h3 class="about__partner">A TRUSTED RECRUITING PARTNER</h3>
      <p class="about__text">We have over 25 years of recruiting and human resources experience. Our recruiters have the expertise, insights, and passion to bring value-added recruiting services to your company. We have track record of excellence.</p>
    </div>
    <div class="photo" role="img" aria-label="Photo of a smiling businesswoman in a grey suit at a desk with a laptop" style="top:395px;left:110px;width:143px;height:140px;background:linear-gradient(160deg,#3a3a3a,#9d9d9d 55%,#e6e6e6)"></div>
    <svg class="swoosh" style="bottom:0" height="80" viewBox="0 0 253 80" preserveAspectRatio="none" aria-hidden="true">
      <path d="M0 30 Q110 70 253 50 L253 80 L0 80 Z" fill="var(--red)"/>
      <path d="M0 22 Q110 60 253 44" stroke="#bbb" stroke-width="3" fill="none"/>
    </svg>
  </article>

  <article class="panel mailer">
    <div class="mailer__stamp" aria-hidden="true"></div>
    <div class="brand mailer__brand"><span class="brand__square"></span>MORVELL STAFFING PARTNERS</div>
    <div class="mailer__contact">
      <div class="mailer__name">Morvell Staffing Partners</div>
      <div class="mailer__phone">PHONE: <strong>555-014-2286</strong></div>
      <div class="mailer__web"><b>Web:</b> www.morvellstaffingpartners.example<br><b>Email:</b> info@morvellstaffingpartners.example</div>
    </div>
  </article>

  <article class="panel cover">
    <div class="brand cover__brand"><span class="brand__square"></span>MORVELL STAFFING PARTNERS</div>
    <div class="photo" role="img" aria-label="Photo of two professional women talking in a bright modern office lounge" style="top:60px;left:0;width:100%;height:210px;background:linear-gradient(180deg,#e9e9e9,#cfcfcf 50%,#8d7f74)"></div>
    <svg class="swoosh" style="top:210px" height="110" viewBox="0 0 253 110" preserveAspectRatio="none" aria-hidden="true">
      <path d="M0 110 L0 70 Q100 80 253 0 L253 110 Z" fill="#fff"/>
      <path d="M0 80 Q110 85 253 8" stroke="var(--red)" stroke-width="6" fill="none"/>
      <path d="M0 95 Q120 95 253 22" stroke="#9a9a9a" stroke-width="3" fill="none"/>
    </svg>
    <div class="cover__welcome">Welcome to</div>
    <h1 class="cover__name">Morvell Staffing<span>Partners</span></h1>
    <div class="cover__url">www.morvellstaffingpartners.example</div>
    <svg class="swoosh" style="bottom:0" height="70" viewBox="0 0 253 70" preserveAspectRatio="none" aria-hidden="true">
      <path d="M0 50 Q130 20 253 45" stroke="var(--red)" stroke-width="2" fill="none"/>
    </svg>
  </article>
</section>

<!-- INSIDE -->
<section class="spread spread--inside">

  <article class="panel intro">
    <h2 class="intro__title">We are a professional search firm specializing in the recruitment of administrative, human resources, and accounting talent.</h2>
    <p class="intro__text">Morvell Staffing Partners is a premier recruitment firm specializing in full-time, permanent placements of administrative, human resources, and accounting talent. We customize each search based on our client's unique requirements. We provide quality, timely, and efficient services. Our recruiters are highly skilled in identifying, screening, interviewing, and assessing candidates across various industries. We can find the right talent for your hiring needs.</p>
    <h2 class="intro__ask">Looking for<br>Great Office<br>Talent?</h2>
    <p class="intro__tag">Let us help you find the right hire for your team! One of our recruiters would be happy to speak with you.</p>
    <div class="photo" role="img" aria-label="Photo of two smiling businesswomen in conversation, one in a purple suit" style="top:400px;left:0;width:100%;height:160px;background:linear-gradient(135deg,#2b2b2b,#6b5a55 45%,#7b5ea8)"></div>
    <svg class="swoosh" style="top:385px" height="40" viewBox="0 0 253 40" preserveAspectRatio="none" aria-hidden="true">
      <path d="M0 0 L253 0 L253 14 Q120 40 0 22 Z" fill="#fff"/>
      <path d="M0 22 Q120 40 253 14" stroke="var(--red)" stroke-width="4" fill="none"/>
    </svg>
  </article>

  <article class="panel services">
    <div class="service" style="top:26px">
      <svg width="38" height="34" viewBox="0 0 38 34" aria-hidden="true"><rect x="9" y="2" width="20" height="10" fill="#fff" stroke="#555"/><rect x="2" y="11" width="34" height="14" rx="2" fill="var(--red)"/><rect x="9" y="20" width="20" height="12" fill="#fff" stroke="#555"/></svg>
      <div><h3>Administrative</h3><p>Behind every successful leader is an awesome assistant. We can provide exceptional support staff who can help you stay organized and run the office smoothly.</p></div>
    </div>
    <div class="service" style="top:110px">
      <svg width="38" height="34" viewBox="0 0 38 34" aria-hidden="true"><circle cx="13" cy="9" r="6" fill="#555"/><path d="M2 30 Q13 14 24 30 Z" fill="#555"/><circle cx="25" cy="11" r="6" fill="var(--red)"/><path d="M14 32 Q25 16 36 32 Z" fill="var(--red)"/></svg>
      <div><h3>Human Resources</h3><p>Human Capital matters. We can provide a results-driven human resources professional who can help take care of your employees and managers while balancing the needs of your company.</p></div>
    </div>
    <div class="service" style="top:205px">
      <svg width="38" height="34" viewBox="0 0 38 34" aria-hidden="true"><rect x="4" y="18" width="8" height="14" fill="var(--red)"/><rect x="15" y="6" width="8" height="26" fill="var(--red)"/><rect x="26" y="12" width="8" height="20" fill="#555"/></svg>
      <div><h3>Accounting</h3><p>If you are seeking an accountant who can keep your company's financial accounts on track, we can help. We have a pipeline of sharp accountants.</p></div>
    </div>
    <svg class="swoosh" style="top:285px" height="40" viewBox="0 0 253 40" preserveAspectRatio="none" aria-hidden="true">
      <path d="M0 34 Q170 40 253 0" stroke="var(--red)" stroke-width="3" fill="none"/>
      <path d="M0 38 Q170 44 253 8" stroke="#c4c4c4" stroke-width="2" fill="none"/>
    </svg>
    <div class="how">
      <h3>How We Work:</h3>
      <ul>
        <li>We provide direct hire contingency based placements. This is no-risk recruiting. There is no fee to pay unless you hire our candidate.</li>
        <li>We offer a 90-Day Placement Guarantee. If you are not satisfied with our candidate after 90 days of employment, we will provide a replacement free of charge.</li>
      </ul>
    </div>
    <svg class="swoosh" style="top:420px" height="40" viewBox="0 0 253 40" preserveAspectRatio="none" aria-hidden="true">
      <path d="M0 10 Q150 40 253 30" stroke="var(--red)" stroke-width="3" fill="none"/>
    </svg>
    <div class="brand services__brand"><span class="brand__square"></span>MORVELL STAFFING PARTNERS</div>
    <div class="services__url">www.morvellstaffingpartners.example</div>
  </article>

  <article class="panel process">
    <h2 class="process__title">Offering a full suite of services<br>to meet your hiring needs</h2>
    <ol class="steps">
      <li class="step"><span class="step__tag"><i></i>STEP 1:</span><p>Intake/Needs Assessment. We learn about your company, hiring department, and job specifications.</p></li>
      <li class="step"><span class="step__tag"><i></i>STEP 2:</span><p>Identifying Candidates. We source, pre-screen, and short list candidates who meet your job requirements, salary range, and interest level.</p></li>
      <li class="step"><span class="step__tag"><i></i>STEP 3:</span><p>Presenting Candidates. We present you with resumes of candidates for your feedback.</p></li>
      <li class="step"><span class="step__tag"><i></i>STEP 4:</span><p>Interview Coordination. We coordinate phone screens and on-site interviews as appropriate.</p></li>
      <li class="step"><span class="step__tag"><i></i>STEP 5:</span><p>Job Offer/Negotiation. We extend the job offer and handle the negotiation process.</p></li>
      <li class="step"><span class="step__tag"><i></i>STEP 6:</span><p>Job Acceptance. Our candidate starts working for your company.</p></li>
      <li class="step"><span class="step__tag"><i></i>STEP 7:</span><p><b>Follow-up.</b> We touch base with the candidate and client every 30 days for the next three months. The purpose is to make sure that the client and candidate are in a mutually satisfying work relationship.</p></li>
    </ol>
    <svg class="swoosh" style="top:365px" height="45" viewBox="0 0 253 45" preserveAspectRatio="none" aria-hidden="true">
      <path d="M0 10 Q120 50 253 8" stroke="var(--red)" stroke-width="3" fill="none"/>
      <path d="M0 16 Q120 54 253 14" stroke="#c4c4c4" stroke-width="2" fill="none"/>
    </svg>
    <div class="difference">
      <h3>Experience the Morvell Difference</h3>
      <ul>
        <li>Top-Notch Talent. We will only present candidates who meet 90% of your job requirements.</li>
        <li>Thorough. We listen to your needs and develop a recruiting checklist to make sure we cover all basis.</li>
        <li>Tenacious. We are passionate and persistent about meeting your expectations.</li>
        <li>Timely. We deliver quality results on time.</li>
      </ul>
    </div>
  </article>
</section>

</body>
</html>
```